Marlow Sail Works President Business Card Carbon fiber catamarans

Hi.. I need a new business card design.. I am the President of a high tech yacht builder. We build Carbon Fiber go fast catamarans... Maybe we use the file I am sharing to you as the back of the card.. We need to look cool and crisp ...

Target Market(s)

Affluent People who will purchase a cool yacht

Industry/Entity Type

Custom Yacht Builder

Contact Information for Business Card

Dean Pellway , President, 731.508.2164 USA

Font styles to use
Serif

Requirements
Must have
• the clean crisp cool feel
Nice to have
• clean and crisp
Should not have
• Bold ugly

```html
<!DOCTYPE html>
<html lang="en">
<head>
<meta charset="utf-8">
<title>Marlow Sail Works – Business Card</title>
<link rel="stylesheet" href="https://fonts.googleapis.com/css2?family=Michroma&family=Mulish:wght@400;500&display=swap">
<style>
  :root {
    --backdrop: #c9c9c9;
    --card-dark: #0d0d0d;
    --card-mid: #1a1a1a;
    --silver: #d6d6d6;
    --silver-soft: #b5b5b5;
    --rule: #555555;
    --icon-bg: #c4c4c4;
    --icon-ink: #2a2a2a;
  }
  * { margin: 0; padding: 0; box-sizing: border-box; }
  html, body { width: 1200px; height: 1200px; overflow: hidden; }
  body {
    background: var(--backdrop);
    position: relative;
    font-family: "Mulish", sans-serif;
  }
  .card {
    position: absolute;
    top: 303px;
    width: 370px;
    height: 594px;
    background: radial-gradient(ellipse at 50% 40%, var(--card-mid), var(--card-dark) 75%);
    box-shadow: 3px 4px 8px rgba(0,0,0,0.45);
    color: var(--silver);
  }
  .card--front { left: 200px; }
  .card--back { left: 600px; }

  /* front */
  .front-badge {
    position: absolute;
    left: 50%;
    top: 120px;
    width: 170px;
    height: 170px;
    margin-left: -85px;
    border-radius: 50%;
    background: var(--silver-soft);
  }
  .front-name {
    position: absolute;
    left: 0; right: 0;
    top: 470px;
    text-align: center;
    font-family: "Michroma", sans-serif;
    color: var(--silver);
  }
  .front-name .line-1 { display: block; font-size: 34px; letter-spacing: 6px; line-height: 40px; }
  .front-name .line-2 { display: block; font-size: 20px; letter-spacing: 4px; line-height: 30px; }

  /* back */
  .back-brand {
    position: absolute;
    left: 40px; right: 30px;
    top: 138px;
    display: flex;
    align-items: center;
    gap: 14px;
  }
  .back-brand .mark-square {
    width: 48px; height: 48px;
    background: var(--silver-soft);
    flex: none;
  }
  .back-brand .brand-name {
    font-family: "Michroma", sans-serif;
    color: var(--silver);
    line-height: 1.25;
  }
  .brand-name .line-1 { display: block; font-size: 22px; letter-spacing: 4px; }
  .brand-name .line-2 { display: block; font-size: 13px; letter-spacing: 3px; }

  .contact {
    position: absolute;
    left: 0; right: 0;
    top: 336px;
    text-align: center;
  }
  .person-name {
    font-family: "Michroma", sans-serif;
    font-size: 15px;
    letter-spacing: 3px;
    color: var(--silver);
  }
  .person-role { font-size: 15px; color: var(--silver-soft); margin-top: 2px; }
  .icon-row {
    display: flex;
    align-items: center;
    justify-content: center;
    gap: 4px;
    margin-top: 18px;
  }
  .icon-row .rule { width: 52px; height: 1px; background: var(--rule); margin: 0 6px; }
  .icon {
    width: 25px; height: 25px;
    background: var(--icon-bg);
    border-radius: 3px;
    display: flex; align-items: center; justify-content: center;
  }
  .details { margin-top: 8px; font-size: 15px; line-height: 23px; color: var(--silver); }
  .details .email, .details .web { color: var(--silver-soft); }
  .divider { width: 195px; height: 1px; background: var(--rule); margin: 12px auto 14px; }
  .address { font-size: 15px; color: var(--silver); }
</style>
</head>
<body>
  <section class="card card--front">
    <div class="front-badge"></div>
    <h1 class="front-name">
      <span class="line-1">MARLOW</span>
      <span class="line-2">SAIL WORKS</span>
    </h1>
  </section>

  <section class="card card--back">
    <div class="back-brand">
      <div class="mark-square"></div>
      <div class="brand-name">
        <span class="line-1">MARLOW</span>
        <span class="line-2">SAIL WORKS</span>
      </div>
    </div>

    <div class="contact">
      <div class="person-name">DEAN PELLWAY</div>
      <div class="person-role">President</div>

      <div class="icon-row">
        <span class="rule"></span>
        <span class="icon">
          <svg width="15" height="15" viewBox="0 0 24 24" fill="var(--icon-ink)">
            <path d="M6.6 10.8a15 15 0 0 0 6.6 6.6l2.2-2.2a1 1 0 0 1 1-.25 11.4 11.4 0 0 0 3.6.57 1 1 0 0 1 1 1V20a1 1 0 0 1-1 1A17 17 0 0 1 3 4a1 1 0 0 1 1-1h3.5a1 1 0 0 1 1 1c0 1.25.2 2.45.57 3.57a1 1 0 0 1-.25 1z"/>
          </svg>
        </span>
        <span class="icon">
          <svg width="15" height="15" viewBox="0 0 24 24" fill="none" stroke="var(--icon-ink)" stroke-width="2">
            <rect x="3" y="5" width="18" height="14"/>
            <path d="M3 5l9 8 9-8"/>
          </svg>
        </span>
        <span class="icon">
          <svg width="15" height="15" viewBox="0 0 24 24" fill="none" stroke="var(--icon-ink)" stroke-width="2">
            <circle cx="12" cy="12" r="9"/>
            <path d="M3 12h18M12 3c3 3 3 15 0 18M12 3c-3 3-3 15 0 18"/>
          </svg>
        </span>
        <span class="rule"></span>
      </div>

      <div class="details">
        <div class="phone">731.508.2164</div>
        <div class="email">info@marlowsail.com</div>
        <div class="web">www.marlowsailworks.com</div>
      </div>
      <div class="divider"></div>
      <div class="address">Rhode Island 02840, USA</div>
    </div>
  </section>
</body>
</html>
```